New Business Card for our Indoor Golf Training Facility

We are looking for designs for a new business card for our indoor golf training facility. Attached is our logo, our logo with our slogan, and here is our elevator pitch (What makes us different from the others) not sure if all the info will fit on one card, maybe you can condense the elevator pitch? here is the info

Elevator Pitch
We work with serious golfers and those that want to be serious golfers…
to make you better, faster, at all phases of the game…
We use the same state-of-the-art technology as professional golfers…
which produces data sets that shows your improvement in real time.
Our facility is available 24/7 to our members, which allows you to improve on your time.

our website: www.birchpinlinks.com

Target Market(s)

Golfers

Font styles to use
Serif
Sans Serif

Colors
ec1f27
f59195
fbd4d5
919191
d3d3d3
1b1b1b

Requirements
Must have
• our logo or our logo with the slogan, elevator pitch (can be condensed or shortened)

```html
<!DOCTYPE html>
<html lang="en">
<head>
<meta charset="utf-8">
<title>Birchpin Links – Business Card</title>
<link rel="stylesheet" href="https://fonts.googleapis.com/css2?family=Roboto:wght@400;700;900&family=Roboto+Condensed:wght@400;700&display=swap">
<style>
  :root {
    --red: #ec1f27;
    --red-band: #e2403a;
    --pink: #f59195;
    --blush: #fbd4d5;
    --grey: #919191;
    --light-grey: #d3d3d3;
    --ink: #1b1b1b;
    --paper: #ffffff;
    --backdrop: #ece9e4;
    --text-grey: #5a5a5a;
  }
  * { box-sizing: border-box; margin: 0; padding: 0; }
  html, body { width: 1200px; height: 911px; overflow: hidden; }
  body {
    background: var(--backdrop);
    font-family: "Roboto", Arial, sans-serif;
    position: relative;
  }
  .card {
    position: absolute;
    top: 295px;
    width: 540px;
    height: 310px;
    border-radius: 16px;
    background: var(--paper);
    overflow: hidden;
    box-shadow: 0 6px 18px rgba(0,0,0,0.18);
  }
  .card--front { left: 40px; }
  .card--back { left: 620px; }

  /* front */
  .brand {
    position: absolute;
    left: 0; right: 0; top: 0; height: 140px;
    display: flex; flex-direction: column; justify-content: center; align-items: center;
  }
  .brand__name {
    font-weight: 900; font-size: 42px; color: var(--red); letter-spacing: -0.5px; line-height: 1;
  }
  .brand__slogan {
    margin-top: 8px; font-size: 14px; color: var(--red); letter-spacing: 0.2px;
  }
  .contact-band {
    position: absolute; left: 0; right: 0; top: 140px; height: 136px;
    background: linear-gradient(180deg, var(--red-band) 0%, var(--red) 100%);
    color: var(--paper);
    text-align: center;
    padding-top: 16px;
  }
  .contact-band__name { font-weight: 700; font-size: 26px; line-height: 1.05; }
  .contact-band__title { font-size: 13px; margin-top: 3px; }
  .contact-band__rule {
    width: 230px; height: 1px; margin: 10px auto 9px;
    background: linear-gradient(90deg, transparent, var(--blush), transparent);
  }
  .contact-band__line { font-size: 13px; line-height: 1.45; }
  .web-strip {
    position: absolute; left: 0; right: 0; bottom: 0; height: 34px;
    background: var(--ink); color: var(--paper);
    display: flex; align-items: center; justify-content: center;
    font-size: 13px; letter-spacing: 0.3px;
  }

  /* back */
  .pitch { position: absolute; inset: 0; text-align: center; padding-top: 40px; }
  .pitch__brand {
    font-weight: 900; font-size: 34px; color: var(--red); line-height: 1; letter-spacing: -0.5px;
  }
  .pitch__heading {
    margin-top: 20px; font-family: "Roboto Condensed", Arial, sans-serif;
    font-weight: 700; font-size: 18px; color: var(--red); letter-spacing: 0.3px;
  }
  .pitch__text {
    margin-top: 8px; font-family: "Roboto Condensed", Arial, sans-serif;
    font-size: 12.5px; line-height: 1.5; color: var(--text-grey);
  }
  .pitch__social { display: flex; justify-content: center; gap: 5px; margin-top: 12px; }
  .pitch__social span { width: 12px; height: 12px; border-radius: 50%; background: var(--red); }
</style>
</head>
<body>
  <section class="card card--front" aria-label="Business card front">
    <div class="brand">
      <span class="brand__name">Birchpin Links</span>
      <p class="brand__slogan">Train Smarter. Play Lower. Every Day.</p>
    </div>
    <div class="contact-band">
      <p class="contact-band__name">Daniel Reyes</p>
      <p class="contact-band__title">CEO/Founder</p>
      <div class="contact-band__rule"></div>
      <p class="contact-band__line">1480 W. Fairway Ave Suite B4, Lakemont, OH 45890</p>
      <p class="contact-band__line">513-555-0172 | info@birchpinlinks.com</p>
    </div>
    <div class="web-strip">www.birchpinlinks.com</div>
  </section>

  <section class="card card--back" aria-label="Business card back">
    <div class="pitch">
      <p class="pitch__brand">Birchpin Links</p>
      <h2 class="pitch__heading">ELEVATOR PITCH:</h2>
      <p class="pitch__text">
        We work with serious golfers and those that want to be serious golfers…<br>
        to make you better, faster, at all phases of the game…<br>
        We use the same state-of-the-art technology as professional golfers…<br>
        which produces data sets that shows your improvement in real time.<br>
        Our facility is available 24/7 to our members, which allows you to improve on your time.
      </p>
      <div class="pitch__social" role="img" aria-label="Social media links"><span></span><span></span></div>
    </div>
  </section>
</body>
</html>
```